Pitch Deck Powerpoint Template for Entrepreneurship/Education Based Nonprofit

I need a stylish powerpoint design for a start-up nonprofit called Harbor Venture Works (HVW). I am building HVWs pitch deck to raise money. HVW is an entrepreneurial incubator and accelerator that seeks to identify, validate, test, and launch innovative ventures that improve public education. An example of our model, and one of our partners, is Kestrel Schools in New Orleans and New York :http://kestrelsch.example.org

We need the deck to look sleek and innovative - like a start-up pitch deck. Lots of different templates and fonts that pop off the page.

Target Market(s)

Individuals, foundations, and any other stakeholder - we are pitching a new business model and asking for money.

Industry/Entity Type

Building

Font styles to use
Sans Serif

Requirements
Must have
• A sleek/modern feel with several different template slides. charts and graphs/ strong fonts that pop off the page, use of the logo:
• It would be great to have a slide describing the 3 primary programs at Harbor Venture Works (HVW):
• - HVWspark - come in with an idea for an innovation in education, and we will do a two day workshop to examine your business assumptions and discuss next steps.
• - HVWpropell - take your idea to a prototype and launch to customers - we help you with an intensive 30 day program
• - HVWnurture - for existing nonprofit projects, we allow you to work under our umbrella to launch and build capacity
• Slides: Problem Definition, Solution, Value Proposition, Data/MEasurement, Key Partners, About the founder, Key Advisors

```html
<!DOCTYPE html>
<html lang="en">
<head>
<meta charset="utf-8">
<title>Our Programs</title>
<link href="https://fonts.googleapis.com/css2?family=Open+Sans:wght@400;600;700&family=Oswald:wght@400;500&display=swap" rel="stylesheet">
<style>
  :root {
    --navy: #0d4580;
    --magenta: #a8228e;
    --white: #ffffff;
    --stage: #000000;
    --ink: #1a1a1a;
    --rule: #0d4580;
  }
  * { box-sizing: border-box; margin: 0; padding: 0; }
  html, body { width: 1200px; height: 1100px; overflow: hidden; background: var(--stage); }
  body { position: relative; font-family: "Open Sans", Arial, sans-serif; }

  .deck-title {
    position: absolute; top: 94px; left: 0; width: 1200px;
    text-align: center; color: var(--white); font-weight: 600; font-size: 32px;
  }
  .deck-number {
    position: absolute; right: 38px; top: 1046px;
    color: var(--navy); font-size: 32px; font-weight: 400;
  }

  .slide {
    position: absolute; left: 88px; top: 166px; width: 1024px; height: 768px;
    background: var(--white); overflow: hidden;
  }
  .title-band {
    position: absolute; left: 0; top: 43px; width: 733px; height: 93px;
    background: var(--navy);
  }
  .title-band h1 {
    position: absolute; left: 45px; top: 18px;
    font-family: "Oswald", "Arial Narrow", sans-serif; font-weight: 400;
    font-size: 44px; color: var(--white); letter-spacing: -0.5px; line-height: 56px;
  }
  .brand {
    position: absolute; left: 760px; top: 48px; width: 250px;
    font-family: "Open Sans", Arial, sans-serif; font-weight: 700;
    font-size: 30px; line-height: 32px; color: var(--navy);
  }

  .programs { position: absolute; left: 0; top: 194px; width: 1024px; height: 436px; }
  .divider { position: absolute; top: 0; width: 1px; height: 434px; background: var(--rule); }
  .divider.one { left: 344px; }
  .divider.two { left: 672px; }

  .program { position: absolute; top: 0; width: 310px; text-align: center; }
  .program.spark { left: 21px; }
  .program.propell { left: 349px; }
  .program.nurture { left: 681px; }

  .badge { display: block; margin: 0 auto; width: 190px; height: 190px; }
  .program h2 {
    margin-top: 24px; font-size: 31px; font-weight: 600; line-height: 40px; color: var(--navy);
  }
  .program.nurture h2 { margin-top: 28px; }
  .program h2 .prefix { color: var(--magenta); }
  .program p {
    margin: 4px auto 0; width: 270px; font-size: 17px; line-height: 27px; color: var(--ink);
  }

  .footer { position: absolute; left: 0; top: 676px; width: 1024px; height: 92px; }
  .footer svg { position: absolute; left: 0; top: 0; }
  .footer .page, .footer .site {
    position: absolute; top: 42px; color: var(--white); font-weight: 700; font-size: 23px;
  }
  .footer .page { left: 45px; }
  .footer .site { right: 54px; }
</style>
</head>
<body>
  <div class="deck-title">Our Programs</div>

  <section class="slide">
    <div class="title-band"><h1>PRIMARY PROGRAMS</h1></div>
    <div class="brand">Harbor Venture Works</div>

    <div class="programs">
      <div class="divider one"></div>
      <div class="divider two"></div>

      <article class="program spark">
        <svg class="badge" viewBox="0 0 190 190" aria-hidden="true">
          <circle cx="95" cy="95" r="92" fill="none" stroke="var(--navy)" stroke-width="1.2"/>
          <circle cx="95" cy="95" r="88" fill="none" stroke="var(--navy)" stroke-width="1"/>
          <g fill="var(--navy)" stroke="var(--navy)">
            <path d="M95 60 a31 31 0 0 0 -18 56 v12 h36 v-12 a31 31 0 0 0 -18 -56z" stroke="none"/>
            <rect x="79" y="131" width="32" height="6" rx="3" stroke="none"/>
            <rect x="83" y="140" width="24" height="6" rx="3" stroke="none"/>
            <g stroke-width="5" stroke-linecap="round">
              <line x1="95" y1="36" x2="95" y2="48"/>
              <line x1="54" y1="90" x2="66" y2="90"/>
              <line x1="124" y1="90" x2="136" y2="90"/>
              <line x1="66" y1="55" x2="74" y2="63"/>
              <line x1="124" y1="55" x2="116" y2="63"/>
              <line x1="66" y1="125" x2="74" y2="117"/>
              <line x1="124" y1="125" x2="116" y2="117"/>
            </g>
          </g>
        </svg>
        <h2><span class="prefix">HVW</span>spark</h2>
        <p>Come in with an idea for an innovation in education, and we will do a two day workshop to examine your business assumptions and discuss next steps.</p>
      </article>

      <article class="program propell">
        <svg class="badge" viewBox="0 0 190 190" aria-hidden="true">
          <circle cx="95" cy="95" r="92" fill="none" stroke="var(--navy)" stroke-width="1.2"/>
          <circle cx="95" cy="95" r="88" fill="none" stroke="var(--navy)" stroke-width="1"/>
          <g fill="var(--navy)">
            <rect x="93" y="72" width="4" height="24"/>
            <path d="M95 80 C80 82 66 72 64 58 C80 56 93 64 95 80z"/>
            <path d="M96 78 C96 60 106 46 122 42 C124 60 112 74 96 78z"/>
            <rect x="66" y="94" width="58" height="12" rx="2"/>
            <path d="M70 110 h50 l-6 34 h-38z"/>
          </g>
        </svg>
        <h2><span class="prefix">HVW</span>propell</h2>
        <p>Take your idea to a prototype and launch to customers - we help you with an intensive 30 day program</p>
      </article>

      <article class="program nurture">
        <svg class="badge" viewBox="0 0 190 190" aria-hidden="true">
          <circle cx="95" cy="95" r="92" fill="none" stroke="var(--navy)" stroke-width="1.2"/>
          <circle cx="95" cy="95" r="88" fill="none" stroke="var(--navy)" stroke-width="1"/>
          <g fill="var(--navy)">
            <rect x="46" y="128" width="7" height="10"/>
            <rect x="57" y="122" width="7" height="16"/>
            <rect x="68" y="124" width="7" height="14"/>
            <rect x="79" y="118" width="7" height="20"/>
            <rect x="90" y="112" width="7" height="26"/>
            <rect x="101" y="106" width="7" height="32"/>
            <rect x="112" y="98" width="7" height="40"/>
            <rect x="123" y="90" width="7" height="48"/>
            <path d="M36 118 L66 90 L84 104 L118 70 L108 60 L138 52 L130 82 L122 74 L84 114 L66 100 L44 124z"/>
          </g>
        </svg>
        <h2><span class="prefix">HVW</span>nurture</h2>
        <p>For existing nonprofit projects, we allow you to work under our umbrella to launch and build capacity</p>
      </article>
    </div>

    <footer class="footer">
      <svg width="1024" height="92" viewBox="0 0 1024 92" aria-hidden="true">
        <defs>
          <pattern id="scallop" x="0" y="0" width="28" height="20" patternUnits="userSpaceOnUse">
            <path d="M0 14 Q7 4 14 10 Q21 16 28 10" fill="none" stroke="var(--navy)" stroke-width="3"/>
          </pattern>
          <pattern id="scallop-fill" x="0" y="0" width="28" height="20" patternUnits="userSpaceOnUse">
            <path d="M0 14 Q7 4 14 10 Q21 16 28 10 V20 H0z" fill="var(--magenta)"/>
          </pattern>
        </defs>
        <rect x="0" y="0" width="1024" height="20" fill="url(#scallop-fill)"/>
        <rect x="0" y="18" width="1024" height="74" fill="var(--magenta)"/>
        <rect x="0" y="0" width="1024" height="20" fill="url(#scallop)"/>
      </svg>
      <span class="page">Page 1</span>
      <span class="site">www.hvw.example.com</span>
    </footer>
  </section>

  <div class="deck-number">24</div>
</body>
</html>
```